Simple but impressive brochure for Consulting Company

We need a single page (back and front) brochure to introduce our company to prospective clients. We are open to different formats, but think that a trifold or double fold may work best. (fold up style brochure or a flyer with front & back).

It should be easy to print as we will need to print it as soon as possible. 8 1/2 x 11 based format is probably best, but again, we are open to suggestions.

About the Company:

We are a consulting company comprised of Harbor Fleet fighter pilots (SKYEDGE), Harbor Fleet DIVERS, and business executives, that use our knowledge and experience in high risk / high performance environments to benefit our business clients. Most of our clients are in the oil and mining sector.

We deal with drilling companies and their crews and management. We do lectures and provide on-site training and coaching.

Enclosed in the "file" section are various one page handouts with information that describes what we do and how we currently project our image to our clients.

Our website is http://www.veltracore.example

We have photographs of worksites, fighter jets, etc. available for creative use, if the quality is deemed acceptable by you, the designer, to use. We are not opposed to stock photos if those would be preferable.

We are working on a fairly tight schedule as we have an event on 4 February 2013. So we need the design done and enough time to have the final version printed. We set this project at 5 days, but can extend it a bit as needed.

We are looking for a design that is solid, professional and gives an indication of our background in high risk environments, but does not over emphasis our military experience.

Oil field related imagery would be a nice addition. In our business, we emphasis and sell the concept of SAFE and RELIABLE operations, done by people with vast experience in the field.

We take our experience in the field and aircraft carrier operations and pass those lessons to the oil field and mining operations. (primarily oil field)

In case you need to know: we have a few different versions of our LOGO in the attached files. It consists of an orb and the word VELTRA in "Good Times" font, slightly flattened and stretched. (you can see the logo files). We also use a Veltra NADIR(tm) logo for a specific set of programs we offer.

Note: We have more files to upload, but currently it is maxed at 5 files. They will be uploaded if more are allowed or put in a Filevault.

Thank you all for your participation.  I'm sorry I could only pick one design, as so many of you are very talented and made the choice difficult.

Target Market(s)

Our buyers are managers and executives of Meridian 400 companies. Primarily male, educated, many with engineering backgrounds.

Industry/Entity Type

Training

Requirements
Must have
• Our primary desire is to convey a sense of action and professionalism to our prospective clients. I'm not sure if we have anything compulsory required with the exception of our logo.

If there is room and it makes sense, we can include the "Honored Wounded Servicemember" logo. (in file section)

Nice to have
• We would like an ongoing relationship with our selected designer. We will have updated brochures and web graphics in the near future.

```html
<!DOCTYPE html>
<html lang="en">
<head>
<meta charset="utf-8">
<title>Veltra Brochure Spread</title>
<link rel="stylesheet" href="https://fonts.googleapis.com/css2?family=Audiowide&family=Arimo:ital,wght@0,400;1,400&family=Varela+Round&display=swap">
<style>
  :root {
    --stage: #eeeeef;
    --paper: #ffffff;
    --navy-deep: #071a36;
    --navy-mid: #14365f;
    --navy-glow: #2a5683;
    --steel: #9a9a9f;
    --ink-light: #eef3f9;
    --sky-top: #7fa6cf;
    --sky-low: #c8b79a;
    --earth: #6c6a5c;
  }
  * { margin: 0; padding: 0; box-sizing: border-box; }
  html, body { width: 1200px; height: 900px; overflow: hidden; background: var(--stage); }
  .spread { position: relative; width: 1200px; height: 900px; }
  .page { position: absolute; top: 45px; width: 502px; height: 805px; background: var(--paper); overflow: hidden; }
  .page--left { left: 108px; }
  .page--right { left: 610px; }

  .panel {
    position: absolute;
    background: radial-gradient(ellipse at 55% 45%, var(--navy-glow) 0%, var(--navy-mid) 40%, var(--navy-deep) 100%);
  }
  .page--left .panel { left: 14px; top: 0; width: 488px; height: 683px; border-top-left-radius: 48px; }
  .page--right .panel { left: 0; top: 88px; width: 490px; height: 608px; border-top-right-radius: 40px; border-bottom-right-radius: 40px; }

  .side-bar { position: absolute; background: var(--steel); }
  .page--left .side-bar--a { left: 2px; top: 170px; width: 12px; height: 120px; }
  .page--left .side-bar--b { left: 0; top: 315px; width: 12px; height: 140px; }
  .page--right .side-bar--a { right: 0; top: 170px; width: 14px; height: 200px; }

  .photo { position: absolute; }
  .photo--jets-formation { left: 0; top: 713px; width: 502px; height: 92px;
    background: linear-gradient(180deg, var(--sky-top) 0%, #8c9cae 45%, var(--earth) 100%); }
  .photo--jet-sky { left: 32px; top: 0; width: 470px; height: 82px;
    background: linear-gradient(90deg, var(--sky-top) 0%, #a9bcd0 55%, var(--sky-low) 100%); }
  .photo--jets-ground { left: 0; top: 715px; width: 290px; height: 90px;
    background: linear-gradient(180deg, #8e9aa6 0%, #7d7a68 60%, var(--earth) 100%); border-top-right-radius: 14px; }

  .rule { position: absolute; height: 3px; background: var(--navy-deep); }
  .rule--steel { background: var(--steel); }

  .tick-row { position: absolute; left: 4px; top: 674px; display: flex; gap: 4px; }
  .tick-row span { width: 10px; height: 10px; background: var(--steel); }

  .stripes { position: absolute; right: 0; width: 205px; height: 6px; background: var(--navy-deep); }
  .stripes--steel { background: var(--steel); }

  .copy { position: absolute; color: var(--ink-light); }
  .brand-title { position: absolute; left: 42px; top: 32px; font-family: "Audiowide", sans-serif; font-size: 33px; color: var(--paper); letter-spacing: 1px; }
  .heading { font-family: "Audiowide", sans-serif; font-size: 12.5px; color: var(--paper); letter-spacing: .3px; text-transform: uppercase; }
  .body { font-family: "Arimo", sans-serif; font-size: 10px; line-height: 17px; }
  .body--italic { font-style: italic; }
  .mission { font-family: "Audiowide", sans-serif; font-size: 12px; line-height: 17px; text-transform: uppercase; color: var(--paper); }

  .list { font-family: "Varela Round", sans-serif; font-size: 11.6px; line-height: 19px; list-style: none; }
  .list li::before { content: "• "; }
  .heading--right { font-size: 13px; line-height: 21px; }
</style>
</head>
<body>
<main class="spread">

  <section class="page page--left">
    <div class="panel"></div>
    <div class="side-bar side-bar--a"></div>
    <div class="side-bar side-bar--b"></div>
    <div class="tick-row"><span></span><span></span><span></span><span></span><span></span><span></span><span></span><span></span><span></span><span></span><span></span><span></span><span></span><span></span><span></span><span></span></div>
    <div class="rule" style="left:0;top:690px;width:502px;"></div>
    <div class="rule rule--steel" style="left:0;top:698px;width:502px;"></div>
    <div class="rule" style="left:0;top:706px;width:502px;"></div>
    <div class="photo photo--jets-formation" role="img" aria-label="Photo of fighter jets flying in formation over farmland"></div>

    <h1 class="brand-title">VELTRA</h1>

    <div class="copy" style="left:40px;top:78px;width:436px;">
      <h2 class="heading">About Veltra</h2>
      <p class="body">Veltra is a high performance training and consulting company with high performance people. Veltra's team consists of Fighter Pilots, Harbor Fleet DIVERS, Special Forces, Astronauts, and veteran industry &amp; corporate leaders. We leverage the credibility, experience, expertise, and ingenuity of our team to develop solutions for our clients.</p>
    </div>

    <div class="copy" style="left:40px;top:175px;width:436px;">
      <h2 class="heading">Veltra's Mission</h2>
    </div>
    <div class="copy" style="left:40px;top:208px;width:440px;">
      <p class="mission">Optimize safety and operational excellence in complex high-risk arenas.</p>
    </div>

    <div class="copy" style="left:40px;top:256px;width:436px;">
      <h2 class="heading">Foundation of Excellence</h2>
      <p class="body">The Foundation of Excellence is built on vision, leadership, communication, and teamwork. Using Veltra practices, high performance companies execute toward a crystal clear strategic vision that leadership clearly communicates to frontline teams and individuals. Veltra's solutions accelerate the realization of an organization's vision.</p>
    </div>

    <div class="copy" style="left:40px;top:354px;width:436px;">
      <h2 class="heading">Engine of Excellence</h2>
      <p class="body">Veltra instills the disciplines of Planning, Briefing, Execution, and the After Action Review (AAR) that raise levels of excellence and drive continuous improvement within an organization.</p>
      <p class="body body--italic" style="margin-top:14px;">The Engine of Excellence yields consistent and predictable results. Our proprietary programs provide disciplined methodologies that create deliberate actions for pursuing your organization's vision.</p>
    </div>

    <div class="copy" style="left:40px;top:484px;width:436px;">
      <h2 class="heading">Human Performance</h2>
      <p class="body">The human element is the most important factor for success in complex high-risk organizations. Veltra laser focuses on the strengths and weaknesses of the human component. Our solutions are built to optimize leadership, decision-making, situational awareness, communications, teamwork, and more.</p>
    </div>

    <div class="copy" style="left:40px;top:580px;width:436px;">
      <h2 class="heading">Veltra NADIR&trade;</h2>
      <p class="body">The quest for zero incidents is the hallmark of high-performing complex high-risk organizations. Our Veltra NADIR&trade; family of programs builds the skill sets required for organizations and individuals to embark on a true Journey of Excellence.</p>
    </div>
  </section>

  <section class="page page--right">
    <div class="photo photo--jet-sky" role="img" aria-label="Photo of a fighter jet on a carrier deck at sunset"></div>
    <div class="rule rule--steel" style="left:0;top:84px;width:502px;"></div>
    <div class="panel"></div>
    <div class="side-bar side-bar--a"></div>
    <div class="rule" style="left:0;top:700px;width:502px;"></div>
    <div class="rule rule--steel" style="left:0;top:707px;width:502px;"></div>
    <div class="photo photo--jets-ground" role="img" aria-label="Photo of fighter jets flying low over open country"></div>
    <div class="stripes" style="top:762px;"></div>
    <div class="stripes stripes--steel" style="top:772px;"></div>
    <div class="stripes" style="top:782px;"></div>

    <div class="copy" style="left:32px;top:104px;width:445px;">
      <h2 class="heading heading--right">The "Human Component"</h2>
      <ul class="list">
        <li>Is the foundation for success in high-risk / high performance operations.</li>
        <li>Is the difference between success or failure and excellence or mediocrity.</li>
        <li>Is the most neglected performance factor in most organizations.</li>
      </ul>
    </div>

    <div class="copy" style="left:32px;top:192px;width:445px;">
      <h2 class="heading heading--right">Veltra NADIR&trade; Program</h2>
      <ul class="list">
        <li>Laser focuses on the "Human Component".</li>
        <li>Builds a foundation for incident free operations.</li>
        <li>Three themed levels of training geared to enhance skills, disciplines,<br>behaviors, and knowledge for operating in high-risk arenas.</li>
        <li>Tailored to each client's operational and organizational needs.</li>
        <li>Focuses on the "non-technical skills" applied by leaders, teams and individuals.</li>
      </ul>
    </div>

    <div class="copy" style="left:32px;top:332px;width:440px;">
      <h2 class="heading heading--right">Develops the foundational skills</h2>
    </div>
    <ul class="copy list" style="left:32px;top:351px;"><li>Planning</li><li>Briefing</li><li>Execution</li></ul>
    <ul class="copy list" style="left:162px;top:351px;"><li>After Action Review</li><li>Continuous Improvement</li></ul>

    <div class="copy" style="left:32px;top:414px;width:320px;">
      <h2 class="heading heading--right">Develops the 7 critical behaviors of high performing teams</h2>
    </div>
    <ul class="copy list" style="left:32px;top:457px;"><li>Leadership</li><li>Assertiveness</li><li>Communications</li><li>Mission Analysis</li></ul>
    <ul class="copy list" style="left:162px;top:471px;"><li>Situational Awareness</li><li>Adaptability and Flexibility</li><li>Decision Making</li></ul>

    <div class="copy" style="left:32px;top:544px;width:300px;">
      <h2 class="heading heading--right">Explores human performance enhancers and detractors</h2>
    </div>
    <ul class="copy list" style="left:32px;top:584px;"><li>Threat and Error Management</li><li>Operational Risk Management</li><li>Teaching and Learning</li><li>Critical Thinking</li><li>Public Speaking Skills</li></ul>
    <ul class="copy list" style="left:268px;top:580px;"><li>Workload Management</li><li>Fatigue</li><li>Stress</li><li>Judgment</li><li>And more...</li></ul>
  </section>

</main>
</body>
</html>
```